Website for my law practice

I am a solo practitioner, who specializes in family law and estate planning in Massachusetts. I need to re-do my website, as it is outdated. I like the idea of a nontraditional law firm website. My website address is: doloresquintanalaw.com. I would like to retain my logo in the green color, as part of the new website. I have uploaded my logo below.

My hourly rate has changed from what is listed on my current website. My new hourly rate is $385.00. Please use this hourly rate when creating the website.

Good morning,

I have reviewed the designs submitted so far. I am happy that the "dq" logo in the green color is part of each of the designs submitted. I am also happy that the standard items seen in law firm websites, such as the scales of justice, etc. were not incorporated. Although the green logo is great, I do not think rest of the website has to have the same green color throughout. Additionally, I was hoping for something more creative, to make the website standout and not the stock web designs you see everyday. Please incorporate more unique images if you can. For example of what I mean, please look at this website: https://www.rosalindfenwicklaw.com

```html
<!DOCTYPE html>
<html lang="en">
<head>
<meta charset="utf-8">
<title>Dolores Quintana, Attorney at Law</title>
<link rel="stylesheet" href="https://fonts.googleapis.com/css2?family=Josefin+Sans:wght@600;700&family=Poppins:wght@400;500;600&display=swap">
<style>
:root{
  --brand-green:#3f8a2e;
  --navy:#1f3a4d;
  --navy-deep:#142836;
  --clay:#c0704a;
  --clay-soft:#e9c7b2;
  --sand:#f4ece0;
  --sand-deep:#ecdfcc;
  --cream:#fbf8f3;
  --ink:#1c1c1c;
  --text:#555;
  --footer:#1b2a35;
  --white:#fff;
  --faq-closed:#f1eee9;
}
*{margin:0;padding:0;box-sizing:border-box}
html,body{width:1200px;height:3646px;overflow:hidden}
body{position:relative;background:var(--white);font-family:"Poppins",sans-serif;color:var(--text)}
.abs{position:absolute}
.heading{font-family:"Josefin Sans",sans-serif;font-weight:700;color:var(--ink)}
.btn{position:absolute;display:flex;align-items:center;justify-content:center;border-radius:30px;font-family:"Poppins",sans-serif;font-weight:600;font-size:15px;text-transform:uppercase;white-space:nowrap}
.btn-main{background:var(--navy);color:var(--white);box-shadow:0 0 0 3px var(--white),0 0 0 5px var(--navy)}
.btn-clay{background:var(--clay);color:var(--white);box-shadow:0 0 0 3px var(--white),0 0 0 5px var(--clay)}

/* header */
.site-header{position:absolute;left:0;top:0;width:1200px;height:85px;background:var(--white)}
.brand{position:absolute;left:96px;top:10px;display:flex;align-items:center;gap:12px}
.brand-mark{width:46px;height:46px;border:3px solid var(--brand-green);border-radius:50%}
.brand-name{color:var(--brand-green);font-family:"Josefin Sans",sans-serif;font-weight:600;font-size:14px;line-height:17px}
.main-nav{position:absolute;left:330px;top:38px;display:flex}
.main-nav a{font-size:12px;color:#333;text-decoration:none;text-transform:uppercase;margin-right:32px}
.main-nav a.active{color:var(--clay);font-weight:600}
.phone-pill{left:938px;top:21px;width:179px;height:46px;background:var(--navy);color:var(--white);font-size:15px;justify-content:flex-start;padding-left:8px;gap:12px}
.phone-pill .ico{width:32px;height:32px;border-radius:50%;background:var(--white);display:flex;align-items:center;justify-content:center}

/* hero */
.hero-photo{left:0;top:85px;width:1200px;height:610px;background:linear-gradient(120deg,#9fb0b6 0%,#64787f 40%,#3c4f5a 70%,#23333f 100%)}
.hero-title{left:0;top:182px;width:1200px;text-align:center;color:var(--white);font-size:46px;line-height:58px}
.hero-sub{left:0;top:312px;width:1200px;text-align:center;color:var(--white);font-size:16px;line-height:31px}
.hero-btn{left:512px;top:393px;width:174px;height:42px}

/* sections */
.section-title{left:0;width:1200px;text-align:center;font-size:45px}
.rule{position:absolute;left:542px;width:106px;height:7px;border-radius:4px;background:var(--clay)}
.lead{font-family:"Josefin Sans",sans-serif;font-weight:700;color:var(--navy);font-size:18px;line-height:33px}
.body-copy{font-size:13.6px;line-height:28.3px;color:var(--text)}

.about-frame{left:620px;top:969px;width:404px;height:387px;border:2px solid var(--clay);border-radius:22px}
.about-photo{left:638px;top:923px;width:433px;height:413px;border-radius:20px;background:linear-gradient(160deg,#a9c4d8,#c8a27f 55%,#8f8f8f)}

.practice-photo{left:133px;top:1639px;width:433px;height:413px;border-radius:22px;background:linear-gradient(135deg,#9aa1a8,#5d6670 50%,#7a3430)}
.practice-frame{left:115px;top:1684px;width:404px;height:388px;border:2px solid var(--navy);border-radius:22px}
.slider-arrow{width:48px;height:48px;border-radius:50%;display:flex;align-items:center;justify-content:center}

/* faq */
.faq-item{position:absolute;left:112px;width:536px;display:flex;align-items:center;justify-content:space-between;padding:0 24px;font-size:16px;line-height:27px;color:#333}
.faq-open{top:2365px;height:49px;background:var(--navy);color:var(--white);width:532px}
.faq-answer{position:absolute;left:112px;top:2414px;width:532px;height:226px;background:var(--sand);padding:20px 22px 0 24px;font-size:13.4px;line-height:27.5px;color:#555}
.faq-closed{background:var(--faq-closed)}
.badge{left:748px;top:2420px;width:272px;height:300px;background:linear-gradient(180deg,#e8d9a8,#d6bd6d);border-radius:14px}

/* cta */
.cta-photo{left:0;top:2844px;width:1200px;height:305px;background:linear-gradient(90deg,#1f3a4d,#2b4d63 60%,#1f3a4d)}
.cta-title{left:112px;top:2972px;color:var(--white);font-size:38px;line-height:48px}
.cta-btn{left:911px;top:2979px;width:176px;height:44px;background:var(--white);color:var(--navy);box-shadow:0 0 0 3px var(--navy),0 0 0 5px var(--white)}

/* footer */
.site-footer{left:0;top:3120px;width:1200px;height:526px;background:var(--footer)}
.foot-brand{left:109px;top:3228px;display:flex;align-items:center;gap:14px}
.foot-brand .brand-mark{width:54px;height:54px}
.foot-head{color:var(--white);font-size:19px;font-weight:500;text-transform:uppercase;top:3248px}
.foot-links{left:391px;top:3310px;list-style:none}
.foot-links li{color:#e6e6e6;font-size:14.5px;line-height:29px}
.contact-list{left:585px;top:3305px;list-style:none}
.contact-list li{color:#e6e6e6;font-size:13.5px;line-height:28.3px;padding-left:20px;position:relative}
.contact-list li.label{font-weight:600}
.contact-list svg{position:absolute;left:0;top:7px}
.foot-map{left:860px;top:3308px;width:215px;height:220px;border-radius:6px;background:linear-gradient(135deg,#eaeaea,#d8d8d8 60%,#e6ddd4)}
.foot-rule{left:109px;top:3579px;width:978px;height:1px;background:#7d8a93}
.copyright{left:0;top:3595px;width:1200px;text-align:center;color:#e6e6e6;font-size:13.5px}
</style>
</head>
<body>

<header class="site-header">
  <div class="brand">
    <span class="brand-mark"></span>
    <span class="brand-name">Dolores Quintana<br>Attorney at Law</span>
  </div>
  <nav class="main-nav">
    <a class="active">Home</a><a>Family Law</a><a>Estate Planning</a><a>About</a><a>Location</a><a>Contact</a><a>FAQ</a>
  </nav>
  <div class="btn phone-pill">
    <span class="ico"><svg width="16" height="16" viewBox="0 0 24 24"><path fill="#1f3a4d" d="M6.6 10.8a15.1 15.1 0 0 0 6.6 6.6l2.2-2.2c.3-.3.7-.4 1-.2 1.1.4 2.3.6 3.6.6.6 0 1 .4 1 1V20c0 .6-.4 1-1 1A17 17 0 0 1 3 4c0-.6.4-1 1-1h3.5c.6 0 1 .4 1 1 0 1.2.2 2.4.6 3.6.1.3 0 .7-.2 1z"/></svg></span>
    555-014-2210
  </div>
</header>

<section>
  <div class="abs hero-photo" role="img" aria-label="Photo of a professional reviewing financial documents at a desk with a laptop"></div>
  <svg class="abs" style="left:0;top:600px" width="1200" height="100" viewBox="0 0 1200 100" aria-hidden="true">
    <path d="M0 10 Q600 90 1200 10 L1200 100 L0 100Z" fill="#fff"/>
    <path d="M0 10 Q600 90 1200 10 L1200 40 Q600 110 0 50Z" fill="#c0704a"/>
  </svg>
  <h1 class="abs heading hero-title">Personalized Legal Solutions for<br>Life’s Biggest Moments.</h1>
  <p class="abs hero-sub">Dolores Quintana is a Solo Practitioner focusing her practice on<br>matters pertaining to family law and estate planning.</p>
  <div class="btn btn-clay hero-btn">Get Started</div>
</section>

<section>
  <h2 class="abs heading section-title" style="top:776px">About Us</h2>
  <div class="rule" style="top:847px"></div>
  <p class="abs lead" style="left:117px;top:942px">Dolores is a graduate of Harborview<br>University in Boston, Massachusetts.</p>
  <p class="abs body-copy" style="left:117px;top:1027px;width:410px">Going through a divorce is difficult. Especially in cases where there are minor children or complicated financial holdings, questions will arise that you may not be prepared to answer without the assistance of a knowledgeable and reputable advocate. Some of the questions that may arise are, will one party remain in the family home or will it be sold? Who will be the primary caretaker of the children? How will custody</p>
  <div class="btn btn-main" style="left:118px;top:1288px;width:174px;height:42px">Read More</div>
  <div class="abs about-frame"></div>
  <div class="abs about-photo" role="img" aria-label="Portrait photo of the attorney outdoors by the water"></div>
</section>

<section>
  <svg class="abs" style="left:0;top:1408px" width="1200" height="780" viewBox="0 0 1200 780" aria-hidden="true">
    <defs><linearGradient id="practiceBg" x1="0" y1="0" x2="0" y2="1"><stop offset="0" stop-color="#f4ece0"/><stop offset="1" stop-color="#ecdfcc"/></linearGradient></defs>
    <path d="M0 0 Q600 75 1200 0 L1200 780 Q600 715 0 780Z" fill="url(#practiceBg)"/>
  </svg>
  <h2 class="abs heading section-title" style="top:1512px">Area of Practice</h2>
  <div class="rule" style="top:1585px"></div>
  <div class="abs practice-photo" role="img" aria-label="Photo of a family meeting with an advisor to sign papers"></div>
  <div class="abs practice-frame"></div>
  <h3 class="abs heading" style="left:621px;top:1652px;font-size:25px;font-weight:600">Family Law</h3>
  <p class="abs lead" style="left:621px;top:1697px;color:var(--clay)">Why Hiring an Attorney is the Right Choice</p>
  <p class="abs body-copy" style="left:629px;top:1738px;width:410px">Going through a divorce is difficult. Especially in cases where there are minor children or complicated financial holdings, questions will arise that you may not be prepared to answer without the assistance of a knowledgeable and reputable advocate. Some of the questions that may arise are, will one party remain in the family home or will it be sold? Who will be the primary caretaker of the children? How will custody</p>
  <div class="btn btn-main" style="left:634px;top:1998px;width:174px;height:42px">Read More</div>
  <div class="abs slider-arrow" style="left:20px;top:1820px;background:#c9bcaa">
    <svg width="18" height="18" viewBox="0 0 24 24"><path d="M15 4 7 12l8 8" stroke="#fff" stroke-width="3" fill="none"/></svg>
  </div>
  <div class="abs slider-arrow" style="left:1129px;top:1820px;background:var(--clay)">
    <svg width="18" height="18" viewBox="0 0 24 24"><path d="m9 4 8 8-8 8" stroke="#fff" stroke-width="3" fill="none"/></svg>
  </div>
</section>

<section>
  <h2 class="abs heading section-title" style="top:2240px;font-size:37px">Frequently Asked Questions</h2>
  <div class="rule" style="top:2305px"></div>
  <div class="faq-item faq-open"><span>What will a divorce cost me?</span><span style="font-size:20px">–</span></div>
  <div class="faq-answer">I currently bill my family law clients at $385.00 per hour. Although I will make every effort to keep costs reasonable for you and work within the agreed upon retainer, I cannot give you a fixed price for a divorce (or any other family law matter). The reason is because I cannot predict what the opposition will file during the litigation process, or what pleadings I may need to file on your behalf in order to achieve your goals in this matter.</div>
  <div class="faq-item faq-closed" style="top:2655px;height:49px"><span>How long will it take for me to get divorced?</span><span style="font-size:22px">+</span></div>
  <div class="faq-item faq-closed" style="top:2717px;height:76px"><span>What kinds of information should I bring with me<br>for my free 30-minute consultation?</span><span style="font-size:22px">+</span></div>
  <div class="abs badge" role="img" aria-label="Client satisfaction award badge"></div>
</section>

<section>
  <div class="abs cta-photo" role="img" aria-label="Navy-tinted photo of hands signing documents"></div>
  <svg class="abs" style="left:0;top:2840px" width="1200" height="70" viewBox="0 0 1200 70" aria-hidden="true">
    <path d="M0 0 L1200 0 L1200 6 Q600 70 0 6Z" fill="#fff"/>
  </svg>
  <h2 class="abs heading cta-title">Here to Help You Plan and Protect<br>What Matters Most.</h2>
  <div class="btn cta-btn">Contact Us</div>
</section>

<footer>
  <div class="abs site-footer"></div>
  <svg class="abs" style="left:0;top:3060px" width="1200" height="90" viewBox="0 0 1200 90" aria-hidden="true">
    <path d="M0 10 Q600 90 1200 10 L1200 60 L0 60Z" fill="#1b2a35"/>
    <path d="M0 0 Q600 85 1200 0 L1200 14 Q600 102 0 14Z" fill="#c0704a"/>
  </svg>
  <div class="abs foot-brand">
    <span class="brand-mark"></span>
    <span class="brand-name">Dolores Quintana<br>Attorney at Law</span>
  </div>
  <h4 class="abs foot-head" style="left:389px">Main Links</h4>
  <h4 class="abs foot-head" style="left:587px">Contact Info</h4>
  <h4 class="abs foot-head" style="left:858px">Our Location</h4>
  <ul class="abs foot-links">
    <li>Home</li><li>Family Law</li><li>Estate Planning</li><li>About</li><li>Location</li><li>Contact</li><li>Faq</li>
  </ul>
  <ul class="abs contact-list">
    <li class="label"><svg width="12" height="14" viewBox="0 0 24 24"><path fill="#fff" d="M6.6 10.8a15.1 15.1 0 0 0 6.6 6.6l2.2-2.2c.3-.3.7-.4 1-.2 1.1.4 2.3.6 3.6.6.6 0 1 .4 1 1V20c0 .6-.4 1-1 1A17 17 0 0 1 3 4c0-.6.4-1 1-1h3.5c.6 0 1 .4 1 1 0 1.2.2 2.4.6 3.6.1.3 0 .7-.2 1z"/></svg>Call Us</li>
    <li>555-014-2210</li>
    <li class="label"><svg width="14" height="12" viewBox="0 0 24 18"><rect x="1" y="1" width="22" height="16" fill="none" stroke="#fff" stroke-width="2"/><path d="M1 1l11 9 11-9" fill="none" stroke="#fff" stroke-width="2"/></svg>Mail Us</li>
    <li>dolores@doloresquintanalaw.com</li>
    <li class="label"><svg width="14" height="13" viewBox="0 0 24 22"><rect x="2" y="6" width="20" height="15" fill="none" stroke="#fff" stroke-width="2"/><rect x="6" y="1" width="12" height="6" fill="none" stroke="#fff" stroke-width="2"/></svg>Fax Us</li>
    <li>555-014-2211</li>
    <li class="label"><svg width="12" height="15" viewBox="0 0 24 30"><path fill="#fff" d="M12 0a11 11 0 0 0-11 11c0 8 11 19 11 19s11-11 11-19A11 11 0 0 0 12 0zm0 15a4 4 0 1 1 0-8 4 4 0 0 1 0 8z"/></svg>Our Location</li>
    <li>42 Alder Lane</li>
    <li>Marlow, MA 01900</li>
  </ul>
  <div class="abs foot-map" role="img" aria-label="Street map showing the office location"></div>
  <div class="abs foot-rule"></div>
  <p class="abs copyright">© 2025 Dolores Quintana I All Rights Reserved</p>
</footer>

</body>
</html>
```